Stationary Set Rebrand for Brennick

We are a Canadian Distribution and Service Company that was established in 1969. Over the past 5 decades we have expanded our business and have warehouses across Canada. We specialize in adhesive tapes, adhesives, films, safety, warehouse, shipping, janitorial and packaging supplies.

We have updated our logo design and would like a new corporate branding identity that includes a new fresh Stationary Set (Business Cards, Letterhead, Letterhead MS Word, Envelope, Presentation Folders, Email Signatures, Notepad Covers, etc.)

Target Market(s)

Industrial Business Sector

Font styles to use
Sans Serif

Colors
0054AA
0677BA
7BADD7
CADEEF
E8F1F8
0094D4
00A9DD
6FCCEA
C7EBF8
E9F6FB
00AB8E
00BBA5
67D7C9
C6EFE9
E9F9F6
EB3D1F
EC4F4E
F09395
F8D3D4
FCEDEE

Requirements
Should not have
• Colors not too light, darker colours preferred

```html
<!DOCTYPE html>
<html lang="en">
<head>
<meta charset="utf-8">
<title>Brennick Business Card</title>
<link rel="stylesheet" href="https://fonts.googleapis.com/css2?family=Nunito:wght@400;600;800&display=swap">
<style>
  :root {
    --canvas-bg: #9a9a9a;
    --card-black: #1c1c1d;
    --edge-red: #d42a2e;
    --accent-red: #e0393b;
    --text-white: #f2f2f2;
    --text-soft: #dcdcdc;
    --pattern-light: #555557;
    --pattern-dark: #0e0e0f;
  }
  * { box-sizing: border-box; margin: 0; padding: 0; }
  html, body {
    width: 1200px; height: 1083px; overflow: hidden;
    background: var(--canvas-bg);
    font-family: "Nunito", sans-serif;
  }
  .stage { position: relative; width: 1200px; height: 1083px; }
  .card {
    position: absolute; left: 300px;
    width: 600px; height: 343px;
    background: var(--card-black);
    border-bottom: 4px solid var(--edge-red);
    box-shadow: 0 14px 30px rgba(0,0,0,0.35);
  }
  .card-front { top: 150px; }
  .card-back { top: 590px; overflow: hidden; }

  .brand {
    position: absolute; left: 44px; top: 44px;
    display: flex; align-items: center; gap: 12px;
  }
  .brand-name {
    font-weight: 800; font-size: 60px; letter-spacing: -1px;
    color: var(--text-white); line-height: 1;
  }
  .brand-mark {
    width: 14px; height: 14px; background: var(--accent-red);
    margin-top: 24px;
  }

  .contact {
    position: absolute; left: 318px; top: 140px;
    color: var(--text-soft); font-size: 15px; line-height: 1.45;
  }
  .contact-name {
    color: var(--accent-red); font-size: 20px; font-weight: 600;
    letter-spacing: 0.5px; line-height: 1.2;
  }
  .contact-title { margin-bottom: 10px; }
  .contact-address { margin-bottom: 10px; }
  .contact-line { display: flex; align-items: center; gap: 8px; }
  .contact-line svg { width: 12px; height: 12px; flex: none; }

  .pattern-area {
    position: absolute; inset: 0;
    background: linear-gradient(115deg, var(--pattern-light) 0%, #2a2a2c 45%, var(--pattern-dark) 100%);
    opacity: 0.9;
  }
  .back-accent {
    position: absolute; right: 118px; bottom: 78px;
    width: 40px; height: 40px; border-radius: 50%;
    background: var(--accent-red);
  }
</style>
</head>
<body>
<main class="stage">
  <section class="card card-front">
    <div class="brand">
      <span class="brand-name">Brennick</span>
      <span class="brand-mark"></span>
    </div>
    <div class="contact">
      <p class="contact-name">EVAN TREMBLAY</p>
      <p class="contact-title">Development Manager Officer</p>
      <p class="contact-address">412 Harbourview Road<br>Unit 18, Surrey, BC V3S 2K7</p>
      <p class="contact-line">
        <svg viewBox="0 0 12 12"><path fill="#e0393b" d="M2.5 0.5l2 2-1 1.3c.6 1.6 1.8 2.9 3.4 3.5l1.3-1 2 2-1.3 1.9C4.5 9.8 2 7 0.7 1.8z"/></svg>
        604-555-0182
      </p>
      <p class="contact-line">
        <svg viewBox="0 0 12 12"><rect x="0.5" y="2" width="11" height="8" fill="#e0393b"/><path d="M0.5 2l5.5 4.5L11.5 2" fill="none" stroke="#1c1c1d" stroke-width="1"/></svg>
        e.tremblay@brennicksupply.ca
      </p>
      <p class="contact-line">
        <svg viewBox="0 0 12 12"><g fill="none" stroke="#e0393b" stroke-width="1"><circle cx="6" cy="6" r="5"/><ellipse cx="6" cy="6" rx="2.2" ry="5"/><path d="M1 6h10M2 3.3h8M2 8.7h8"/></g></svg>
        brennicksupply.ca
      </p>
    </div>
  </section>

  <section class="card card-back">
    <div class="pattern-area" role="img" aria-label="Repeating pattern of glossy leaf motifs fading from grey to black"></div>
    <span class="back-accent"></span>
  </section>
</main>
</body>
</html>
```